Update our OBGYN business card look and info

We are an OBGYN office. Our logo is nice but would like to "woman" part of the logo to be a darker color, to contrast with the flower that surrounds it. Maybe make our practice name Bloom Harbor Health more feminine. Our practice caters to women only. All providers and staff are female.

Target Market(s)

Females 16-65.

Industry/Entity Type

Business

Contact Information for Business Card

See attached upload. The ONLY CHANGE to the information is DELETE the name Paula Renwick, Midwife and REPLACE with Dora Fintelli, Midwife

Logo Text

Bloom Harbor Health Obstetrics & Gynecology

Font styles to use
Serif
Script

Colors
85cae6
0692cd
33a6d7
85abd2
f59195
eea4c8
cadf82
fac994
d3a5cc

```html
<!DOCTYPE html>
<html lang="en">
<head>
<meta charset="utf-8">
<title>Bloom Harbor Health – Business Card</title>
<link href="https://fonts.googleapis.com/css2?family=Tinos&display=swap" rel="stylesheet">
<style>
  :root {
    --page-bg: #e9e4de;
    --card-white: #ffffff;
    --wave-blue: #1ea5d2;
    --address-blue: #2aa6d6;
    --brand-pink: #e8838b;
    --card-pink: #eeb2b9;
    --card-pink-deep: #d98f99;
    --back-pink-light: #ebb0b8;
    --back-pink-dark: #cd8690;
    --ink-light: #ffffff;
  }
  * { box-sizing: border-box; margin: 0; padding: 0; }
  html, body {
    width: 1200px; height: 780px; overflow: hidden;
    background: var(--page-bg);
    font-family: "Tinos", "Times New Roman", serif;
  }
  .canvas { position: relative; width: 1200px; height: 780px; }
  .card {
    position: absolute; top: 241px;
    width: 520px; height: 297px;
    border-radius: 14px; overflow: hidden;
    box-shadow: 0 6px 18px rgba(0,0,0,.18);
  }
  .card--front { left: 50px; background: var(--card-white); }
  .card--back {
    left: 630px;
    background: radial-gradient(ellipse at 50% 45%, var(--back-pink-light) 0%, var(--back-pink-dark) 100%);
  }
  .card__art { position: absolute; inset: 0; width: 100%; height: 100%; }

  .brand { position: absolute; left: 28px; top: 92px; display: flex; align-items: center; gap: 10px; color: var(--brand-pink); }
  .brand__dot { width: 22px; height: 22px; border-radius: 50%; background: var(--wave-blue); flex: none; }
  .brand__name { font-size: 26px; line-height: 1.05; font-weight: 400; }
  .brand__line { display: block; }
  .brand__sub { display: block; font-size: 11.5px; letter-spacing: .12em; text-transform: uppercase; margin-top: 4px; }

  .address {
    position: absolute; right: 165px; top: 20px;
    color: var(--address-blue); font-size: 12.5px; line-height: 1.35;
    text-align: right; white-space: nowrap;
  }
  .providers {
    position: absolute; left: 128px; top: 184px;
    color: var(--ink-light); font-size: 13px; line-height: 1.32; list-style: none;
  }
  .contact {
    position: absolute; left: 318px; top: 196px;
    color: var(--ink-light); font-size: 12px; line-height: 1.6; list-style: none;
    white-space: nowrap;
  }
  .contact__item { display: flex; align-items: center; gap: 6px; }
  .contact__icon { width: 13px; height: 13px; flex: none; }

  .back__brand {
    position: absolute; left: 0; right: 0; top: 118px;
    display: flex; justify-content: center; align-items: center; gap: 10px;
    color: var(--ink-light);
  }
  .back__dot { width: 18px; height: 18px; border-radius: 50%; background: var(--ink-light); }
  .back__name { font-size: 26px; }
  .back__web {
    position: absolute; left: 0; right: 0; top: 168px;
    text-align: center; color: var(--ink-light); font-size: 12.5px; letter-spacing: .14em;
  }
</style>
</head>
<body>
<main class="canvas">

  <section class="card card--front" aria-label="Business card front">
    <svg class="card__art" viewBox="0 0 520 297" preserveAspectRatio="none" aria-hidden="true">
      <path d="M392 0 C362 90 302 140 182 160 C92 175 32 210 10 297 L520 297 L520 0 Z" fill="var(--wave-blue)"/>
      <path d="M406 0 C376 90 316 140 196 160 C106 175 46 210 24 297 L520 297 L520 0 Z" fill="var(--card-white)"/>
      <defs>
        <linearGradient id="frontPink" x1="0" y1="0" x2="1" y2="1">
          <stop offset="0" stop-color="var(--card-pink)"/>
          <stop offset="1" stop-color="var(--card-pink-deep)"/>
        </linearGradient>
      </defs>
      <path d="M410 0 C380 90 320 140 200 160 C110 175 50 210 28 297 L520 297 L520 0 Z" fill="url(#frontPink)"/>
    </svg>

    <div class="brand">
      <span class="brand__dot"></span>
      <span class="brand__name">
        <span class="brand__line">Bloom Harbor Health</span>
        <span class="brand__sub">Obstetrics &amp; Gynecology</span>
      </span>
    </div>

    <p class="address">418 Linden Row, Ste 3B<br>Harbor Falls, GA 30917-4420</p>

    <ul class="providers">
      <li>Marian Okafor, MD</li>
      <li>Lena Sorvino, MD</li>
      <li>Ruth Calloway, MD</li>
      <li>Hannah Pruitt, Midwife</li>
      <li>Dora Fintelli, Midwife</li>
    </ul>

    <ul class="contact">
      <li class="contact__item">
        <svg class="contact__icon" viewBox="0 0 14 14" aria-hidden="true"><circle cx="7" cy="7" r="6.3" fill="none" stroke="#fff" stroke-width="1"/><path d="M4.6 3.8c.4-.3.8-.2 1 .2l.6 1.2c.1.3 0 .6-.2.8l-.4.3c.4.9 1.1 1.6 2 2l.3-.4c.2-.2.5-.3.8-.2l1.2.6c.4.2.5.6.2 1l-.5.6C8 10.6 3.4 6 4 4.3z" fill="#fff"/></svg>
        <span>555-214-3870</span>
      </li>
      <li class="contact__item">
        <svg class="contact__icon" viewBox="0 0 14 14" aria-hidden="true"><circle cx="7" cy="7" r="6.3" fill="none" stroke="#fff" stroke-width="1"/><rect x="4.3" y="3.6" width="5.4" height="2.4" fill="#fff"/><rect x="3.4" y="6.2" width="7.2" height="3" rx=".6" fill="#fff"/><rect x="4.6" y="9" width="4.8" height="1.6" fill="#fff"/></svg>
        <span>555-214-3925</span>
      </li>
      <li class="contact__item">
        <svg class="contact__icon" viewBox="0 0 14 14" aria-hidden="true"><circle cx="7" cy="7" r="6.3" fill="none" stroke="#fff" stroke-width="1"/><circle cx="7" cy="7" r="3.6" fill="none" stroke="#fff" stroke-width=".9"/><path d="M3.4 7h7.2M7 3.4c-1.4 1.8-1.4 5.4 0 7.2M7 3.4c1.4 1.8 1.4 5.4 0 7.2" fill="none" stroke="#fff" stroke-width=".8"/></svg>
        <span>www.bloomharborhealth.com</span>
      </li>
    </ul>
  </section>

  <section class="card card--back" aria-label="Business card back">
    <div class="back__brand">
      <span class="back__dot"></span>
      <span class="back__name">Bloom Harbor Health</span>
    </div>
    <p class="back__web">www.bloomharborhealth.com</p>
  </section>

</main>
</body>
</html>
```